Business Card Design Project

This is the first time we use our new logo. We need a business card that we can use both on our institutional corporate relationships and also that works for our staff that deals with consumers directly.

VELUNDA is a new company dedicated to empower consumers and to provide them with the best choices for specialized health care using the latest telemedicine technology (medicine at a distance via videoconference).

We want to print this cards in high quality materials and process. We will like designs that allow us to use UV spot varnish and other techniques that will differentiate us.

We are including Two different versions of Color logos. In addition we are including white over black background logos. Those can be used replacing the black for a color.

Please note this is the first time we will be creating any corporate materials with our new logo and colors.

Target Market(s)

34+ consumers of medium high and high socioeconomic levels.

Industry/Entity Type

Health

Requirements
Must have
• Our logo on its original colors
Should not have
• Any other graphical element or design that is not our logo

```html
<!DOCTYPE html>
<html lang="en">
<head>
<meta charset="utf-8">
<title>VELUNDA Business Card</title>
<link rel="stylesheet" href="https://fonts.googleapis.com/css2?family=Montserrat:wght@400;700&family=Arimo:wght@400&display=swap">
<style>
  :root {
    --stage: #ece8e3;
    --paper: #ffffff;
    --navy: #1b527f;
    --sky: #5fb3e0;
    --teal: #00a89c;
    --ink: #2a2a2a;
    --rule: #c9c9c9;
    --white: #ffffff;
  }
  * { margin: 0; padding: 0; box-sizing: border-box; }
  html, body {
    width: 1200px; height: 1057px; overflow: hidden;
    background: var(--stage);
  }
  .stage { position: relative; width: 1200px; height: 1057px; }

  .card {
    position: absolute; left: 220px; width: 760px; height: 434px;
    overflow: hidden; box-shadow: 0 6px 18px rgba(0,0,0,.18);
  }
  .card-front { top: 60px; background: var(--paper); }
  .card-back  { top: 563px; background: var(--teal); }

  .wave { position: absolute; inset: 0; width: 760px; height: 434px; }

  .brand {
    position: absolute; left: 92px; top: 78px;
    display: flex; align-items: center; gap: 18px;
  }
  .brand-dot { width: 44px; height: 44px; border-radius: 50%; background: var(--teal); }
  .brand-name {
    font-family: "Montserrat", sans-serif; font-weight: 700;
    font-size: 62px; letter-spacing: 4px; color: var(--navy);
  }

  .address {
    position: absolute; left: 40px; top: 180px; width: 232px;
    text-align: right; font-family: "Arimo", sans-serif; font-style: normal;
    font-size: 18px; line-height: 26px; color: var(--ink);
  }
  .divider {
    position: absolute; left: 290px; top: 176px; width: 1px; height: 92px;
    background: var(--rule);
  }
  .contacts {
    position: absolute; left: 308px; top: 174px; list-style: none;
    font-family: "Arimo", sans-serif; font-size: 18px; line-height: 24px; color: var(--ink);
  }
  .contacts li { display: flex; align-items: center; gap: 8px; }
  .contacts svg { width: 14px; height: 14px; flex: none; }

  .holder {
    position: absolute; left: 38px; top: 374px;
    font-family: "Montserrat", sans-serif; color: var(--white); white-space: nowrap;
  }
  .holder-name { font-weight: 700; font-size: 28px; }
  .holder-title { font-weight: 400; font-size: 19px; }

  .back-name {
    position: absolute; left: 0; right: 0; top: 150px; text-align: center;
    font-family: "Montserrat", sans-serif; font-weight: 700;
    font-size: 76px; letter-spacing: 6px; color: var(--white);
  }
  .back-url {
    position: absolute; left: 0; right: 0; bottom: 52px; text-align: center;
    font-family: "Arimo", sans-serif; font-size: 24px; letter-spacing: 7px; color: var(--white);
  }
</style>
</head>
<body>
<main class="stage">

  <section class="card card-front" aria-label="Business card front">
    <svg class="wave" viewBox="0 0 760 434" aria-hidden="true">
      <path d="M0,318 C160,312 320,300 470,292 C600,284 700,220 760,120" fill="none" stroke="var(--sky)" stroke-width="5"/>
      <path d="M0,330 C160,324 320,312 470,304 C600,296 700,232 760,134 L760,160 C700,260 600,330 480,350 C420,360 380,400 330,434 L0,434 Z" fill="var(--navy)"/>
      <path d="M352,434 C400,402 440,374 500,364 C610,344 710,272 760,182" fill="none" stroke="var(--sky)" stroke-width="4"/>
    </svg>

    <div class="brand">
      <span class="brand-dot"></span>
      <span class="brand-name">VELUNDA</span>
    </div>

    <address class="address">Street Name<br>City Name<br>State, City Zip Code</address>
    <span class="divider"></span>

    <ul class="contacts">
      <li><svg viewBox="0 0 14 14"><path d="M3 1l2.5 3-1.5 1.5c.8 1.8 2.2 3.2 4 4L9.5 8 12.5 10.5 11 13C6 12.5 1.5 8 1 3z" fill="var(--ink)"/></svg>014-555-0182</li>
      <li><svg viewBox="0 0 14 14"><path d="M3 1l2.5 3-1.5 1.5c.8 1.8 2.2 3.2 4 4L9.5 8 12.5 10.5 11 13C6 12.5 1.5 8 1 3z" fill="var(--ink)"/></svg>014-555-0182</li>
      <li><svg viewBox="0 0 14 14"><rect x="1" y="3" width="12" height="8" fill="none" stroke="var(--ink)" stroke-width="1.5"/><path d="M1 3l6 5 6-5" fill="none" stroke="var(--ink)" stroke-width="1.5"/></svg>name@velunda.com</li>
      <li><svg viewBox="0 0 14 14"><circle cx="7" cy="7" r="5.5" fill="none" stroke="var(--ink)" stroke-width="1.3"/><path d="M1.5 7h11M7 1.5c-3 3.5-3 7.5 0 11M7 1.5c3 3.5 3 7.5 0 11" fill="none" stroke="var(--ink)" stroke-width="1"/></svg>www.velunda.com</li>
    </ul>

    <p class="holder"><span class="holder-name">Your Name</span><span class="holder-title">, Title</span></p>
  </section>

  <section class="card card-back" aria-label="Business card back">
    <p class="back-name">VELUNDA</p>
    <p class="back-url">www.velunda.com</p>
  </section>

</main>
</body>
</html>
```